Supplement Brand Product Labels

Product Label for Supplement Brand

Protein Powder Label (2 x different flavours)

Neon Colours / Skull / Spooky
Refer to pictures below, they are the look we are wanting to go with but put our touch to it aswell.

Target Market(s)

Fitness

Industry/Entity Type

Supplement Brand

Colors
0054AA
0677BA
7BADD7
CADEEF
E8F1F8
0094D4
00A9DD
6FCCEA
C7EBF8
E9F6FB
00AB8E
00BBA5
67D7C9
C6EFE9
E9F9F6
59FF00
82FF00
B8FF75
E3FFCB
F4FFEA
FFF300
FFF600
FEFA6F
FFFEC7
FFFEE8
FFC000
F8CF3A
FAE287
FDF2CF
FEFAEE
F0912C
F2A743
F7CA91
FBE8D2
FDF5EE
EE7325
F08F49
F5BC92
FAE3D3
FDF4ED
EB3D1F
EC4F4E
F09395
F8D3D4
FCEDEE
E54698
E96AAD
F1A4CE
F9D9EA
FCEFF6
A7469A
B969AE
D3A5CF
EDDBEB
F8F0F9
6B429C
8869AF
B7A5CE
E3DAEB
F3F0F8

Requirements
Nice to have
• Skull, Neon Colours, Abstract, Barbell, Lighting Bolt, Flames, Spooky

```html
<!DOCTYPE html>
<html lang="en">
<head>
<meta charset="utf-8">
<title>Korvex Supps – Creatine Monohydrate Label</title>
<link href="https://fonts.googleapis.com/css2?family=Roboto+Slab:wght@700&family=Ubuntu:wght@400;500;700&family=Russo+One&display=swap" rel="stylesheet">
<style>
  :root {
    --bg-deep: #120a22;
    --bg-violet: #2a1550;
    --neon-pink: #e54698;
    --neon-purple: #6b429c;
    --neon-blue: #0054aa;
    --neon-green: #82ff00;
    --neon-yellow: #fff300;
    --ink: #ffffff;
    --ink-soft: #f3f0f8;
  }
  * { box-sizing: border-box; margin: 0; padding: 0; }
  html, body { width: 1200px; height: 548px; overflow: hidden; background: var(--bg-deep); }
  .label {
    position: relative; width: 1200px; height: 548px; overflow: hidden;
    background:
      radial-gradient(ellipse 380px 300px at 1020px 80px, rgba(107,66,156,.35), transparent 70%),
      radial-gradient(ellipse 300px 260px at 260px 90px, rgba(107,66,156,.25), transparent 70%),
      linear-gradient(180deg, #1c0f33 0%, var(--bg-deep) 60%, #0d0818 100%);
    color: var(--ink); font-family: "Ubuntu", sans-serif;
  }
  .artwork {
    position: absolute; left: 380px; top: 0; width: 420px; height: 548px;
    background:
      radial-gradient(ellipse 150px 110px at 210px 130px, rgba(229,70,152,.95), transparent 75%),
      radial-gradient(ellipse 190px 170px at 210px 250px, rgba(107,66,156,.85), transparent 75%),
      radial-gradient(ellipse 120px 90px at 140px 440px, rgba(130,255,0,.35), transparent 75%),
      radial-gradient(ellipse 120px 90px at 290px 420px, rgba(255,192,0,.30), transparent 75%),
      radial-gradient(ellipse 210px 280px at 210px 300px, rgba(42,21,80,.9), transparent 80%);
  }
  .directions { position: absolute; left: 28px; top: 50px; width: 298px; }
  .section-title { font-family: "Roboto Slab", serif; font-weight: 700; font-size: 15.5px; margin-bottom: 10px; }
  .directions p { font-size: 11.5px; line-height: 16.5px; text-align: justify; }
  .directions .usage { text-align: left; margin-bottom: 21px; }
  .directions .store { font-weight: 700; margin-top: 21px; }
  .brand {
    position: absolute; font-family: "Ubuntu", sans-serif; font-weight: 700;
    color: var(--ink); letter-spacing: 1px; line-height: 1;
  }
  .brand-center { left: 520px; top: 140px; width: 150px; text-align: center; font-size: 30px; }
  .brand-corner { left: 50px; top: 445px; font-size: 32px; }
  .product-name {
    position: absolute; left: 400px; top: 266px; width: 390px; text-align: center;
    font-family: "Russo One", sans-serif; font-size: 38px; line-height: 49px; letter-spacing: 2px;
  }
  .net-weight {
    position: absolute; left: 540px; top: 486px; width: 110px; text-align: center;
    font-family: "Russo One", sans-serif; font-size: 21px;
  }
  .nutrition {
    position: absolute; left: 872px; top: 50px; width: 300px; height: 286px;
    border: 2px solid var(--ink); border-collapse: collapse; font-size: 11px;
  }
  .nutrition th {
    font-weight: 500; font-size: 9.5px; line-height: 12px; text-align: center;
    border-bottom: 2px solid var(--ink); padding: 6px 4px 5px; height: 48px; vertical-align: middle;
  }
  .nutrition th:first-child { text-align: left; padding-left: 8px; }
  .nutrition td { height: 29.7px; padding: 0 4px; text-align: center; }
  .nutrition td:first-child { text-align: left; padding-left: 8px; white-space: nowrap; }
  .nutrition .sub td:first-child { padding-left: 20px; }
  .nutrition td:nth-child(2) { text-align: left; padding-left: 8px; }
  .ingredients { position: absolute; left: 882px; top: 368px; }
  .ingredients p { font-size: 11.5px; padding-left: 3px; margin-top: -2px; }
  .origin-badge { position: absolute; left: 862px; top: 480px; }
</style>
</head>
<body>
<main class="label">
  <div class="artwork" role="img" aria-label="Neon pink, purple and green glowing skull illustration wrapped in smoke"></div>

  <section class="directions">
    <h2 class="section-title">Directions Of Use</h2>
    <p class="usage">Mix 5g (1 scoop) with 250ml's of cold water and consume immediately.</p>
    <p>Formulated supplementary sports food. Not suitable for children under 15 years of age or pregnant women. Should only be used under medical or dietetic supervision. This product is not a sole source of nutrition and should be consumed in conjunction with a nutritious diet and appropriate physical training or exercise</p>
    <p class="store">Store in a cool dry place out of direct sunlight.</p>
  </section>

  <div class="brand brand-center">Korvex</div>
  <h1 class="product-name">CREATINE<br>MONOHYDRATE</h1>
  <div class="net-weight">250G</div>
  <div class="brand brand-corner">Korvex</div>

  <table class="nutrition">
    <thead>
      <tr>
        <th>50 Servings<br>Per 250g Packet<br>5 Grams Per Serve</th>
        <th>Average Quantity<br>Per Serving</th>
        <th>Average Quantity<br>Per 100g</th>
      </tr>
    </thead>
    <tbody>
      <tr><td>Energy (KJ)</td><td>0</td><td>0</td></tr>
      <tr><td>Protein (G)</td><td>0</td><td>0</td></tr>
      <tr><td>Fat (G)</td><td>0</td><td>0</td></tr>
      <tr class="sub"><td>(Saturated) (G)</td><td>0</td><td>0</td></tr>
      <tr><td>Total Carbohydrates (G)</td><td>0</td><td>0</td></tr>
      <tr class="sub"><td>(Sugar) (G)</td><td>0</td><td>0</td></tr>
      <tr><td>Sodium (MG)</td><td>0</td><td>0</td></tr>
      <tr><td>Creatine Monohydrate (G)</td><td>5</td><td>100</td></tr>
    </tbody>
  </table>

  <section class="ingredients">
    <h2 class="section-title">Ingredients</h2>
    <p>Creatine Monohydrate.</p>
  </section>

  <svg class="origin-badge" width="144" height="32" viewBox="0 0 144 32" role="img" aria-label="Country of origin badge">
    <rect x="0" y="0" width="144" height="32" rx="4" fill="var(--ink)"/>
  </svg>
</main>
</body>
</html>
```